Fitness Equipment Repair Business Needs a Catchy New Business Card

We have an existing business card, however, it is quite plain and boring. We are expanding primarily in the commercial area (gyms, studios, apartment complexes etc). The business card will serve as eye candy to those managers/owners that can't be met for a face to face.
Originally I was planning for a brochure as well, but all of our information is better summarized on our website. (brightloopservice.ca).
I would like the card to match the colour scheme of the website and utilize the logo. It should have a professional clean feel to it, however, a little colouring outside the lines wouldn't hurt.
The example card is for my service technician (Colin Marsh). If possible I would like to be able to edit the text to use for more than one person.

Industry/Entity Type

Appliance Repair

Contact Information for Business Card

Clean, crisp and professional but needs to be eye catching. Preferably using the black, white and red colour scheme matching the website. Double sided would be nice, but is not necessary.

Colors
ec1f27
ffffff
000000

Requirements
Must have
• Must be able to edit name, phone number and title to use for multiple people. Must show the company website (brightloopservice.ca).

```html
<!DOCTYPE html>
<html lang="en">
<head>
<meta charset="utf-8">
<title>Brightloop Service – Business Card</title>
<link rel="stylesheet" href="https://fonts.googleapis.com/css2?family=Noto+Serif:wght@400;700&family=Montserrat:wght@500&display=swap">
<style>
  :root {
    --brand-red: #ec1f27;
    --brand-white: #ffffff;
    --brand-black: #000000;
    --card-black: #151515;
    --card-black-edge: #0c0c0c;
    --band-grey: #efefef;
    --ink-dark: #222222;
    --stage: #d9d6d0;
  }
  * { margin: 0; padding: 0; box-sizing: border-box; }
  html, body { width: 1200px; height: 780px; overflow: hidden; }
  body {
    background: var(--stage);
    display: flex;
    align-items: center;
    justify-content: center;
    gap: 40px;
    font-family: "Noto Serif", Georgia, serif;
  }
  .card {
    position: relative;
    width: 540px;
    height: 309px;
    background: radial-gradient(circle at 40% 35%, var(--card-black) 0%, var(--card-black-edge) 100%);
    box-shadow: 0 10px 28px rgba(0,0,0,.35);
    overflow: hidden;
    color: var(--brand-white);
  }

  /* Front */
  .brand-block {
    position: absolute;
    left: 40px; top: 95px;
    width: 200px;
    display: flex; align-items: center; gap: 10px;
  }
  .brand-dot { width: 14px; height: 14px; border-radius: 50%; background: var(--brand-red); flex: none; }
  .brand-name { font-size: 22px; font-weight: 700; line-height: 1.15; color: var(--brand-white); }
  .separator {
    position: absolute;
    left: 262px; top: 40px;
    width: 1px; height: 170px;
    background: linear-gradient(to bottom, rgba(255,255,255,0), rgba(255,255,255,.7), rgba(255,255,255,0));
  }
  .contact {
    position: absolute;
    left: 290px; top: 30px;
    font-size: 12px; line-height: 1.45;
  }
  .person-name { font-size: 20px; font-weight: 700; line-height: 1.1; }
  .person-title { color: var(--brand-red); font-size: 13px; margin-bottom: 12px; }
  .address { margin-bottom: 12px; }
  .contact-list { list-style: none; }
  .contact-list li { display: flex; align-items: center; gap: 8px; }
  .contact-list svg { width: 11px; height: 11px; flex: none; }
  .accent-line {
    position: absolute; left: 0; right: 0; bottom: 54px;
    height: 4px; background: var(--brand-red);
  }
  .tagline-band {
    position: absolute; left: 0; right: 0; bottom: 0;
    height: 54px; background: var(--band-grey);
    display: flex; align-items: center; justify-content: center;
    color: var(--ink-dark); font-size: 14px;
  }

  /* Back */
  .card-back { display: flex; align-items: center; justify-content: center; }
  .back-brand { display: flex; align-items: center; gap: 14px; }
  .back-brand .brand-dot { width: 18px; height: 18px; }
  .back-wordmark {
    font-family: "Montserrat", Arial, sans-serif;
    font-weight: 500; font-size: 26px;
    font-variant: small-caps; letter-spacing: 1px;
  }
</style>
</head>
<body>

<section class="card card-front" aria-label="Card front">
  <div class="brand-block">
    <span class="brand-dot"></span>
    <span class="brand-name">Brightloop Service</span>
  </div>
  <div class="separator"></div>
  <div class="contact">
    <p class="person-name">Colin Marsh</p>
    <p class="person-title">service technician</p>
    <p class="address">118 Larkspur Row NW<br>Edmonton AB T5K 2P4</p>
    <ul class="contact-list">
      <li><svg viewBox="0 0 12 12"><rect x="3" y="0.5" width="6" height="11" rx="1" fill="var(--brand-red)"/></svg>555-014-2286</li>
      <li><svg viewBox="0 0 12 12"><rect x="1" y="3" width="10" height="7" rx="1" fill="var(--brand-red)"/><rect x="3" y="1" width="6" height="3" fill="var(--brand-red)"/></svg>780-555-0193</li>
      <li><svg viewBox="0 0 12 12"><rect x="0.5" y="2" width="11" height="8" fill="var(--brand-red)"/><path d="M0.5 2 L6 7 L11.5 2" stroke="var(--card-black)" fill="none"/></svg>brightloop@mailhub.ca</li>
      <li><svg viewBox="0 0 12 12"><circle cx="6" cy="6" r="5.5" fill="var(--brand-red)"/><path d="M0.5 6 H11.5 M6 0.5 V11.5" stroke="var(--card-black)" stroke-width="0.8"/></svg>www.brightloopservice.ca</li>
    </ul>
  </div>
  <div class="accent-line"></div>
  <div class="tagline-band">when your equipment can't finish the workout, give us a call !</div>
</section>

<section class="card card-back" aria-label="Card back">
  <div class="back-brand">
    <span class="brand-dot"></span>
    <span class="back-wordmark">Brightloop Service</span>
  </div>
</section>

</body>
</html>
```